Design a single page Shopify store web page

We are looking to have a page designed for a single page Shopify store with 2 products. We already have a basic structure that we like, though we are open to suggestions. We are looking for somebody to provide a design/color scheme that we can then implement using Shopify's templating system. We can handle the implementation(HTML / CSS / jS) as we already have 2 web developers on the team, but have not been able to find a design we liked.

The job would consist of providing a mockup (photoshop or otherwise) and any vector graphics you choose to create for the site (we can provide product photos and other images).

You can also look at http://brickdune.com.au for some of our design direction we have used so far

Target Market(s)

Young Australian Males (18 - 49)

Industry/Entity Type

Store

Number of Pages Required

1 page

Font styles to use
Serif
Sans Serif

Requirements
Must have
• Single Page Design
• E-commerce Product Purchase
• Manly (whatever interpretation of that you have)

```html
<!DOCTYPE html>
<html lang="en">
<head>
<meta charset="utf-8">
<title>Dune Packs</title>
<link rel="stylesheet" href="https://fonts.googleapis.com/css2?family=PT+Sans+Narrow:wght@400;700&family=Open+Sans:wght@700&display=swap">
<style>
  :root {
    --red: #d9233a;
    --navy: #23273a;
    --navy-glass: rgba(30, 33, 48, 0.88);
    --white: #ffffff;
    --ink: #1c1c22;
    --hero-top: #5a6283;
    --hero-mid: #3d4463;
    --hero-low: #2c3150;
  }
  * { box-sizing: border-box; margin: 0; padding: 0; }
  html, body { width: 1200px; height: 999px; overflow: hidden; background: var(--white); }
  body { font-family: "PT Sans Narrow", "Arial Narrow", sans-serif; color: var(--ink); position: relative; }

  .hero-photo {
    position: absolute; left: 0; top: 0; width: 1200px; height: 643px;
    background:
      radial-gradient(ellipse 420px 380px at 600px 320px, #7a6a78 0%, rgba(122,106,120,0) 70%),
      linear-gradient(180deg, var(--hero-top) 0%, var(--hero-mid) 55%, var(--hero-low) 100%);
  }

  .site-header {
    position: absolute; left: 0; top: 0; width: 1200px; height: 71px;
    background: var(--navy-glass);
  }
  .brand {
    position: absolute; left: 150px; top: 9px;
    font-family: "PT Sans Narrow", sans-serif; font-weight: 700;
    font-size: 42px; color: var(--white); letter-spacing: 0.5px;
  }
  .main-nav { position: absolute; left: 491px; top: 0; display: flex; }
  .main-nav a {
    display: block; height: 53px; line-height: 68px; padding: 0 15px;
    color: var(--white); text-decoration: none; font-size: 16px; text-transform: uppercase;
    margin-right: 1px;
  }
  .main-nav a.is-active { background: var(--red); border-bottom: 4px solid #b81c30; line-height: 64px; padding: 0 13px; }
  .main-nav a.plans { margin-left: 16px; }
  .signup-button {
    position: absolute; left: 949px; top: 17px; width: 101px; height: 34px;
    background: var(--red); color: var(--white); font-weight: 700; font-size: 17px;
    text-align: center; line-height: 35px; text-decoration: none;
  }

  .hero-headline {
    position: absolute; left: 0; top: 346px; width: 1200px; text-align: center;
    color: var(--white); font-weight: 700; font-size: 33px; line-height: 43px;
  }
  .hero-headline em { font-style: normal; color: var(--red); }

  .launch-form {
    position: absolute; left: 150px; top: 535px; width: 900px; height: 108px;
    background: var(--navy-glass);
  }
  .launch-label {
    position: absolute; top: 12px; width: 419px; text-align: center;
    color: var(--red); font-size: 15px;
  }
  .launch-label.left { left: 22px; }
  .launch-label.right { left: 464px; }
  .email-field {
    position: absolute; left: 22px; top: 49px; width: 419px; height: 44px;
    background: var(--white); text-align: center; line-height: 44px; font-size: 20px; color: var(--ink);
  }
  .notify-button {
    position: absolute; left: 464px; top: 49px; width: 419px; height: 44px;
    background: var(--red); color: var(--white); text-align: center; line-height: 44px; font-size: 20px;
  }

  .steps-title {
    position: absolute; left: 0; top: 692px; width: 1200px; text-align: center;
    font-weight: 700; font-size: 27px; text-transform: uppercase;
  }
  .step {
    position: absolute; top: 763px; width: 290px; height: 140px;
    background: var(--red); color: var(--white);
  }
  .step svg.step-icon { position: absolute; left: 14px; top: 30px; }
  .step h3 { position: absolute; left: 90px; top: 34px; font-size: 17px; font-weight: 700; text-transform: uppercase; }
  .step p { position: absolute; left: 90px; top: 56px; width: 190px; font-size: 16px; line-height: 17px; }
  .step-number {
    position: absolute; left: 50%; top: 119px; width: 46px; height: 46px; margin-left: -23px;
    border-radius: 50%; background: var(--white); border: 2px solid var(--red);
    font-family: "Open Sans", sans-serif; font-weight: 700; font-size: 20px;
    color: var(--ink); text-align: center; line-height: 42px;
  }
</style>
</head>
<body>
  <div class="hero-photo" role="img" aria-label="Two young men in open flannel shirts and briefs leaning against a brick wall"></div>

  <header class="site-header">
    <div class="brand">Dune Packs</div>
    <nav class="main-nav">
      <a class="is-active" href="#">How it works</a>
      <a class="plans" href="#">Plans</a>
      <a href="#" style="margin-left:8px">FAQ</a>
      <a href="#" style="margin-left:8px">About us</a>
    </nav>
    <a class="signup-button" href="#">SIGN UP</a>
  </header>

  <h1 class="hero-headline">New <em>Underwear</em> and <em>Socks</em> Delivered to<br>Your Door Every <em>3</em> or <em>6</em> Month</h1>

  <form class="launch-form">
    <div class="launch-label left">Let me know when you launch</div>
    <div class="launch-label right">Get a free gift&nbsp; with your first pack</div>
    <div class="email-field">Enter Your Email</div>
    <div class="notify-button">Notify Me</div>
  </form>

  <h2 class="steps-title">How it works</h2>

  <section class="step" style="left:150px">
    <svg class="step-icon" width="74" height="66" viewBox="0 0 74 66" fill="none" stroke="#fff" stroke-width="4">
      <rect x="3" y="13" width="48" height="48"/>
      <path d="M13 33 L27 48 L68 4" stroke-width="7" stroke-linejoin="miter"/>
    </svg>
    <h3>Choose a plan</h3>
    <p>There will be plans for all budgets and styles.</p>
    <div class="step-number">1</div>
  </section>

  <section class="step" style="left:456px">
    <svg class="step-icon" width="60" height="70" viewBox="0 0 60 70" fill="none" stroke="#fff" stroke-width="3" stroke-linecap="round" stroke-linejoin="round">
      <path d="M10 12 a10 10 0 1 1 18 0"/>
      <path d="M15 38 V14 a4 4 0 0 1 8 0 V34 V28 a4 4 0 0 1 8 0 V34 V30 a4 4 0 0 1 8 0 V36 V33 a4 4 0 0 1 8 0 V48 c0 10 -6 16 -16 16 h-6 c-6 0 -10 -4 -13 -9 L6 42 a4 4 0 0 1 7 -4 z"/>
    </svg>
    <h3>Choose how often</h3>
    <p>Decide whether you would like to receive new packages every 3 or 6 months.</p>
    <div class="step-number">2</div>
  </section>

  <section class="step" style="left:760px">
    <svg class="step-icon" width="64" height="60" viewBox="0 0 64 60" fill="#fff">
      <rect x="32" y="6" width="22" height="20"/>
      <rect x="39" y="6" width="8" height="7" fill="#d9233a"/>
      <path d="M0 30 h12 v20 h-12 z"/>
      <path d="M14 32 h14 c6 0 10 4 16 4 h-14 v4 h18 l14 -8 c3 -2 6 1 4 4 l-16 12 c-3 2 -6 3 -10 3 h-26 z"/>
    </svg>
    <h3>Get your pack</h3>
    <p>We'll send out your first pack right away and then again every 3 or 6 months.</p>
    <div class="step-number">3</div>
  </section>
</body>
</html>
```